Start up Events company needs a business card design

We are a brand new start up events company that need an impressively designed business card to make the best first impression with our future clients.

Description on company:
- start-up company
- in the events management industry
- selling flagship children related event
- our future clients will mostly be vendors in the alternative education industry. dance schools, music schools, sports camp facilitators, academic establishments
- our target market are kids, parents of kids, mass market

What we need in the business card:
- we currently have a rough design that I have uploaded. we need to brush it up. make it look more professional, more vibrant but keep the meaning of the company which is called "Lantern & Kite"
- a reason for the "Lantern & Kite" concept is because we will be starting off with a flagship event & be branching out into all other related businesses relating to our core highlight which is kids & alternative education.
- this is a tentative logo we have selected - which is a girl on a swing. to represent momentum as a start up company and related to children
- if you have a better logo alternative, please do suggest it to us
- we need more colours, vibrancy yet it has to be sleek and professional.

As we are a start-up company, our budget is tight. If you have a good idea / concept, do take on this project overlooking the tight budget.
If you require any additional information, do feel free to drop us messages!

Thank you designers!

```html
<!DOCTYPE html>
<html lang="en">
<head>
<meta charset="utf-8">
<title>Lantern &amp; Kite – Business Card</title>
<link rel="stylesheet" href="https://fonts.googleapis.com/css2?family=Orbitron:wght@700&family=Exo+2:wght@400;500&display=swap">
<style>
  :root {
    --page: #e6e6e4;
    --card-white: #ffffff;
    --ink: #111111;
    --band-grey: #c9c9c9;
    --pill-shade: #e4e4e4;
    --accent-blue: #1e9ec4;
    --accent-blue-dark: #0d7fa3;
    --text-grey: #3a3a3a;
  }
  * { box-sizing: border-box; margin: 0; padding: 0; }
  html, body {
    width: 1200px;
    height: 1019px;
    overflow: hidden;
    background: var(--page);
  }
  .sheet {
    width: 1200px;
    height: 1019px;
    display: flex;
    flex-direction: column;
    align-items: center;
    justify-content: center;
    gap: 56px;
  }
  .card {
    position: relative;
    width: 760px;
    height: 434px;
    border-radius: 4px;
    overflow: hidden;
    box-shadow: 0 10px 28px rgba(0,0,0,0.18);
    background: var(--card-white);
  }
  .card-art {
    position: absolute;
    inset: 0;
    width: 100%;
    height: 100%;
  }
  .swing-mark {
    position: absolute;
    left: 150px;
    top: 120px;
    width: 120px;
    height: 118px;
    border-radius: 40% 45% 30% 50%;
    background: var(--ink);
  }
  .identity {
    position: absolute;
    right: 44px;
    top: 46px;
    text-align: right;
  }
  .identity-name {
    font-family: "Orbitron", sans-serif;
    font-weight: 700;
    font-size: 30px;
    letter-spacing: 1px;
    color: var(--ink);
    text-transform: uppercase;
  }
  .identity-role {
    font-family: "Exo 2", sans-serif;
    font-weight: 500;
    font-size: 19px;
    color: var(--text-grey);
    margin-top: 2px;
  }
  .contact-icons {
    position: absolute;
    right: 44px;
    top: 136px;
    display: flex;
    gap: 9px;
  }
  .contact-icons svg { width: 17px; height: 17px; }
  .contact-list {
    position: absolute;
    right: 44px;
    top: 166px;
    list-style: none;
    text-align: right;
    font-family: "Exo 2", sans-serif;
    font-size: 14.5px;
    line-height: 25px;
    color: var(--text-grey);
  }
</style>
</head>
<body>
<main class="sheet">

  <!-- Front of card -->
  <section class="card card-front" aria-label="Business card front">
    <svg class="card-art" viewBox="0 0 760 434" aria-hidden="true">
      <defs>
        <linearGradient id="pillFill" x1="0" y1="0" x2="0" y2="1">
          <stop offset="0" stop-color="#ffffff"/>
          <stop offset="1" stop-color="#f1f1f1"/>
        </linearGradient>
        <filter id="pillShadow" x="-10%" y="-10%" width="120%" height="130%">
          <feDropShadow dx="0" dy="4" stdDeviation="6" flood-color="#000" flood-opacity="0.22"/>
        </filter>
      </defs>
      <path class="band-grey" d="M0,230 C160,320 360,390 560,434 L0,434 Z" fill="var(--band-grey)"/>
      <path class="band-black-left" d="M0,320 C110,380 220,415 330,434 L0,434 Z" fill="var(--ink)"/>
      <path class="band-black" d="M760,210 C620,320 470,395 330,434 L470,434 C590,392 690,330 760,290 Z" fill="var(--ink)"/>
      <path class="card-pill" d="M760,34 L210,34 A148,148 0 0 0 210,330 L760,330 Z" fill="url(#pillFill)" filter="url(#pillShadow)"/>
    </svg>

    <div class="swing-mark" role="img" aria-label="Silhouette of a girl on a swing"></div>

    <header class="identity">
      <h1 class="identity-name">Maya Thornfield</h1>
      <p class="identity-role">Managing Director</p>
    </header>

    <div class="contact-icons" aria-hidden="true">
      <svg viewBox="0 0 20 20"><path d="M5 2 L8 2 L9 6 L7 7.5 C8 10 10 12 12.5 13 L14 11 L18 12 L18 15 C18 16.5 17 17.5 15.5 17.5 C8.5 17 3 11.5 2.5 4.5 C2.5 3 3.5 2 5 2 Z" fill="var(--accent-blue)"/></svg>
      <svg viewBox="0 0 20 20"><rect x="5" y="1.5" width="10" height="17" rx="2" fill="var(--accent-blue)"/><rect x="6.7" y="3.5" width="6.6" height="11" fill="#fff"/></svg>
      <svg viewBox="0 0 20 20"><rect x="2" y="4" width="16" height="12" rx="1.5" fill="var(--accent-blue)"/><path d="M2.5 5 L10 11 L17.5 5" stroke="#fff" stroke-width="1.5" fill="none"/></svg>
      <svg viewBox="0 0 20 20"><circle cx="10" cy="10" r="8" fill="var(--accent-blue)"/><path d="M2 10 H18 M10 2 C6 6 6 14 10 18 M10 2 C14 6 14 14 10 18" stroke="#fff" stroke-width="1.2" fill="none"/></svg>
      <svg viewBox="0 0 20 20"><path d="M10 1.5 C6.4 1.5 4 4.2 4 7.4 C4 11.8 10 18.5 10 18.5 C10 18.5 16 11.8 16 7.4 C16 4.2 13.6 1.5 10 1.5 Z" fill="var(--accent-blue)"/><circle cx="10" cy="7.4" r="2.4" fill="#fff"/></svg>
    </div>

    <ul class="contact-list">
      <li>020 555 0142</li>
      <li>020 555 0187</li>
      <li>hello@lanternkite.com</li>
      <li>www.lanternkite.com</li>
      <li>27 Orchard Lane, Level 4, Riverside</li>
    </ul>
  </section>

  <!-- Back of card -->
  <section class="card card-back" aria-label="Business card back">
    <svg class="card-art" viewBox="0 0 760 434" aria-hidden="true">
      <defs>
        <linearGradient id="backBlue" x1="0" y1="0" x2="1" y2="1">
          <stop offset="0" stop-color="var(--accent-blue)"/>
          <stop offset="1" stop-color="var(--accent-blue-dark)"/>
        </linearGradient>
        <radialGradient id="discFill" cx="0.5" cy="0.4" r="0.6">
          <stop offset="0" stop-color="#ffffff"/>
          <stop offset="1" stop-color="#e9e9e9"/>
        </radialGradient>
      </defs>
      <rect width="760" height="434" fill="url(#backBlue)"/>
      <path d="M0,0 L520,0 C430,120 300,200 0,230 Z" fill="#d6d6d6"/>
      <path d="M0,0 L470,0 C390,100 260,170 0,190 Z" fill="#f3f3f3"/>
      <circle cx="470" cy="250" r="215" fill="#5fc0dd" opacity="0.55"/>
      <circle cx="470" cy="250" r="185" fill="url(#discFill)"/>
    </svg>
  </section>

</main>
</body>
</html>
```